Veranix - Solution provider in business consulting

Veranix is a swiss based company providing solutions for developing markets. The business covers various fields of business consulting, such as supply chain, product costs, quality management and manufacturing management. The Business operates in a efficient, straight and solution oriented manner.
The final design should communicate these characteristics. Asian people as well as as western people shall identify the qualities of the company at first sight.
The customer needs business cards with a simple view but an recognizable design, printed in high quality. Engraved elements such as the globe or simple words are possible.
Available colors are: (RAL)
102/102/102
51/102/102
153/204/153
255/102/51
Font: Calibri

```html
<!DOCTYPE html>
<html lang="en">
<head>
<meta charset="utf-8">
<title>Veranix – Business Cards</title>
<link rel="stylesheet" href="https://fonts.googleapis.com/css2?family=Carlito:wght@400;700&display=swap">
<style>
  :root {
    --backdrop: #d6d6d4;
    --card-black: #000000;
    --card-grey: #666666;
    --art-dark: #1c1c1c;
    --art-light: #6a6a6a;
    --swoosh: #d0d0d0;
    --logo-grey: #8a8a8a;
    --text-light: #ffffff;
    --card-w: 620px;
    --card-h: 354px;
  }
  * { box-sizing: border-box; margin: 0; padding: 0; }
  html, body {
    width: 1200px; height: 900px; overflow: hidden;
    background: var(--backdrop);
    font-family: "Carlito", "Calibri", sans-serif;
  }
  .sheet {
    width: 1200px; height: 900px;
    display: flex; flex-direction: column;
    align-items: center; justify-content: center; gap: 60px;
  }
  .card {
    position: relative;
    width: var(--card-w); height: var(--card-h);
    overflow: hidden;
    box-shadow: 0 6px 18px rgba(0,0,0,0.18);
  }
  /* Front side */
  .card--front {
    background: var(--card-black);
    display: flex; align-items: center; justify-content: center; gap: 18px;
  }
  .brand-mark {
    width: 46px; height: 46px; border-radius: 50%;
    background: var(--logo-grey);
  }
  .brand-name {
    color: var(--logo-grey);
    font-size: 72px; font-weight: 400; letter-spacing: 1px;
    line-height: 1;
  }
  /* Back side */
  .card--back { background: var(--card-grey); }
  .card-art { position: absolute; inset: 0; width: 100%; height: 100%; }
  .contact {
    position: absolute; right: 28px; top: 96px;
    text-align: right; color: var(--text-light);
  }
  .contact__name { font-size: 22px; font-weight: 700; line-height: 1.1; }
  .contact__role { font-size: 16px; margin-bottom: 16px; }
  .contact__address { font-size: 16px; line-height: 1.25; margin-bottom: 18px; }
  .contact__list { list-style: none; font-size: 16px; line-height: 1.5; }
  .contact__list li { display: flex; justify-content: flex-end; align-items: center; gap: 10px; }
  .contact__icon { width: 14px; height: 14px; flex: none; }
</style>
</head>
<body>
<main class="sheet">
  <section class="card card--front" aria-label="Card front">
    <span class="brand-name">veranix</span>
    <span class="brand-mark" aria-hidden="true"></span>
  </section>

  <section class="card card--back" aria-label="Card back">
    <svg class="card-art" viewBox="0 0 620 354">
      <defs>
        <linearGradient id="art-fill" x1="0" y1="0" x2="0" y2="1">
          <stop offset="0" stop-color="var(--art-dark)"/>
          <stop offset="1" stop-color="var(--art-light)"/>
        </linearGradient>
      </defs>
      <path d="M300 0 H336 C410 90 395 250 270 320 C225 345 170 354 130 354 H115 C170 350 220 335 262 305 C372 230 380 90 300 0 Z" fill="var(--swoosh)"/>
      <path d="M0 0 H300 C380 90 372 230 262 305 C220 335 170 350 115 354 H0 Z" fill="var(--card-black)"/>
      <circle role="img" aria-label="Engraved globe illustration" cx="168" cy="180" r="128" fill="url(#art-fill)"/>
    </svg>

    <div class="contact">
      <p class="contact__name">Marco Thaler</p>
      <p class="contact__role">CEO</p>
      <p class="contact__address">Veranix GmbH Lindenweg 14<br>8400 Talbach Switzerland</p>
      <ul class="contact__list">
        <li>+41 79 555 0182
          <svg class="contact__icon" viewBox="0 0 14 14"><rect x="3.5" y="1" width="7" height="12" rx="1.2" fill="none" stroke="#fff" stroke-width="1.3"/><circle cx="7" cy="11" r="0.8" fill="#fff"/></svg>
        </li>
        <li>+41 71 555 0347
          <svg class="contact__icon" viewBox="0 0 14 14"><path d="M3 1.5 L5.5 4 L4.3 5.7 C5 7.4 6.6 9 8.3 9.7 L10 8.5 L12.5 11 L11 12.6 C6.5 12.3 1.7 7.5 1.4 3 Z" fill="#fff"/></svg>
        </li>
        <li>marco.thaler@veranix.ch
          <svg class="contact__icon" viewBox="0 0 14 14"><rect x="1" y="3" width="12" height="8" fill="#fff"/><path d="M1 3 L7 8 L13 3" fill="none" stroke="var(--card-grey)" stroke-width="1"/></svg>
        </li>
        <li>www.veranix.ch
          <svg class="contact__icon" viewBox="0 0 14 14"><circle cx="7" cy="7" r="6" fill="#fff"/><path d="M1 7 H13 M7 1 C4 4 4 10 7 13 M7 1 C10 4 10 10 7 13" fill="none" stroke="var(--card-grey)" stroke-width="0.9"/></svg>
        </li>
      </ul>
    </div>
  </section>
</main>
</body>
</html>
```